Switch Kit - Banking Flyer

We want a design for an 8.5x11" flyer that matches the look of our website (www.morvellcommercebank.com). Outline is attached, but please feel free to include images/pictures/graphics that you think makes this easy to understand. The goal is to hand this flyer to a potential customer to get them to understand the information easily and quickly.

```html
<!DOCTYPE html>
<html lang="en">
<head>
<meta charset="utf-8">
<title>Switch Kit – Morvell Commerce Bank Flyer</title>
<link href="https://fonts.googleapis.com/css2?family=Poppins:wght@400;500;600;700;800&display=swap" rel="stylesheet">
<style>
  :root {
    --navy: #22426f;
    --gold: #8c5a14;
    --backdrop: #cfcfcf;
    --paper: #ffffff;
    --ink: #1b1b1b;
  }
  * { box-sizing: border-box; margin: 0; padding: 0; }
  html, body {
    width: 1200px; height: 1000px; overflow: hidden;
    background: var(--backdrop);
    font-family: "Poppins", sans-serif;
  }
  .sheet {
    position: absolute; top: 179px; width: 496px; height: 641px;
    background: var(--paper); overflow: hidden;
  }
  .sheet--front { left: 87px; }
  .sheet--back { left: 618px; }

  /* Front */
  .front-header {
    height: 158px; background: var(--navy); color: #fff;
    text-align: center; padding-top: 26px;
  }
  .front-header h1 {
    font-weight: 800; line-height: 1.05; letter-spacing: -0.3px;
  }
  .front-header h1 .line-1 { display: block; font-size: 23px; }
  .front-header h1 .line-2 { display: block; font-size: 29px; }
  .front-header p {
    font-size: 11.2px; line-height: 13.8px; margin: 18px 22px 0;
    text-align: center;
  }
  .hero {
    position: relative; height: 366px;
  }
  .hero-photo {
    position: absolute; inset: 0;
    background: linear-gradient(160deg, #c9d3dc 0%, #9aa8b8 30%, #2f3f55 55%, #b98a5c 85%, #d9a877 100%);
  }
  .hero-photo::after {
    content: ""; position: absolute; left: 0; right: 0; bottom: 0; height: 110px;
    background: linear-gradient(to bottom, rgba(232,190,150,0), rgba(232,190,150,0.85));
  }
  .hero-brand {
    position: absolute; top: 36px; left: 0; right: 0; text-align: center;
    font-size: 26px; font-weight: 700; color: var(--navy);
  }
  .hero-brand .mark {
    display: inline-block; width: 18px; height: 18px; background: var(--gold);
    margin-right: 10px; vertical-align: -1px;
  }
  .hero-caption {
    position: absolute; left: 0; right: 0; bottom: 10px; text-align: center;
    font-size: 13.6px; line-height: 17px; color: var(--ink);
  }
  .hero-caption strong { display: block; color: var(--gold); font-weight: 700; }
  .step-list { list-style: none; margin: 14px 0 0 92px; }
  .step-list li {
    display: flex; align-items: center; gap: 6px;
    color: var(--gold); font-weight: 700; font-size: 12px; line-height: 14.5px;
    margin-bottom: 8px;
  }
  .step-num {
    flex: none; width: 20px; height: 20px; border-radius: 50%;
    background: var(--gold); color: #fff; font-size: 12px; font-weight: 800;
    display: flex; align-items: center; justify-content: center;
  }

  /* Back */
  .back-header {
    height: 118px; display: flex; align-items: center; justify-content: center;
    border-bottom: 6px solid var(--navy);
  }
  .back-brand { font-size: 26px; font-weight: 700; color: var(--navy); }
  .back-brand .mark {
    display: inline-block; width: 18px; height: 18px; background: var(--gold);
    margin-right: 10px; vertical-align: -1px;
  }
  .step-detail { padding: 26px 22px 0; color: var(--navy); }
  .step-detail section { margin-bottom: 18px; }
  .step-detail h2 {
    color: var(--gold); font-size: 14px; font-weight: 600; line-height: 15.5px;
  }
  .step-detail p { font-size: 11.8px; line-height: 13.7px; }
  .back-footer {
    position: absolute; left: 0; right: 0; bottom: 0; height: 89px;
    background: var(--navy); color: #fff;
    display: flex; align-items: center; justify-content: space-between;
    padding: 0 50px 0 46px;
  }
  .contact { display: flex; align-items: center; gap: 12px; }
  .contact address { font-style: normal; font-size: 11.5px; line-height: 13.7px; font-weight: 500; }
  .contact--phone span { font-size: 17px; font-weight: 700; }
</style>
</head>
<body>

<article class="sheet sheet--front">
  <header class="front-header">
    <h1><span class="line-1">SWITCHING IS EASY</span><span class="line-2">AS 1-2-3!</span></h1>
    <p>One of the main reasons people don’t switch banks is that it can be a hassle. At Morvell Commerce Bank we make it easy. We value your time and with our efficient three step process, switching banks has never been easier.</p>
  </header>

  <div class="hero">
    <div class="hero-photo" role="img" aria-label="Photo of business people reviewing documents at a desk with a laptop"></div>
    <div class="hero-brand"><span class="mark"></span>Morvell Commerce Bank</div>
    <p class="hero-caption">We look forward to creating an exceptional experience for you at<strong>Morvell Commerce Bank</strong></p>
  </div>

  <ol class="step-list">
    <li><span class="step-num">1</span>Open a Morvell Commerce Bank Account</li>
    <li><span class="step-num">2</span>Stop using your old account and redirect your<br>automatic payments and direct deposits.</li>
    <li><span class="step-num">3</span>Close your old account</li>
  </ol>
</article>

<article class="sheet sheet--back">
  <header class="back-header">
    <div class="back-brand"><span class="mark"></span>Morvell Commerce Bank</div>
  </header>

  <div class="step-detail">
    <section>
      <h2>1. Open a Morvell Commerce Bank Account</h2>
      <p>Stop by our branch and visit with our knowledgeable team to open your new account.<br>We will be happy to assist you in choosing the right account for your banking needs.</p>
    </section>
    <section>
      <h2>2. Stop using your old account and redirect your automatic payments and direct deposits</h2>
      <p>It is important to remember to keep your old account open to ensure all your outstanding checks, deposits, and automatic withdrawals have cleared.<br>We will provide you with a Payments Checklist to help you determine the companies you may need to notify of your account change so they can redirect any deposits or automatic withdrawals.<br>Our Direct Deposit Change Notification and Notification of Automatic Withdrawal Change forms will easily allow companies to redirect your direct deposit(s) and automatic withdrawals to your new Morvell Commerce Bank account.</p>
    </section>
    <section>
      <h2>3. Close your old account</h2>
      <p>Now you are ready to switch. We will even provide an Account Closure Authorization form to close your old account. Any remaining account balance will be transferred to your Morvell Commerce Bank account.</p>
    </section>
  </div>

  <footer class="back-footer">
    <div class="contact contact--address">
      <svg width="24" height="34" viewBox="0 0 24 34" aria-hidden="true">
        <path d="M12 2C6.5 2 3 6 3 11c0 6 9 15 9 15s9-9 9-15c0-5-3.5-9-9-9z" fill="#fff"/>
        <circle cx="12" cy="11" r="3.6" fill="var(--navy)"/>
        <ellipse cx="12" cy="29" rx="10" ry="3" fill="none" stroke="#fff" stroke-width="1.4"/>
      </svg>
      <address>2240 East Camelback Road,<br>Suite 310<br>Phoenix, AZ 85016</address>
    </div>
    <div class="contact contact--phone">
      <svg width="30" height="30" viewBox="0 0 30 30" aria-hidden="true">
        <path d="M7 3l4 6-2.5 2.5c1.5 3.5 4.5 6.5 8 8L19 17l6 4-2 4c-1 1.2-3 1.5-5 .8C10 23 5 17 3 10c-.6-2 0-4 1-5z" fill="#fff"/>
        <path d="M17 8a5 5 0 0 1 5 5M17 4a9 9 0 0 1 9 9" fill="none" stroke="#fff" stroke-width="1.8" stroke-linecap="round"/>
      </svg>
      <span>480.555.0142</span>
    </div>
  </footer>
</article>

</body>
</html>
```